Design 4 pages for an event discovery website

This is a contest for the design of 4 pages for an events discovery website. The feature is part of the new sign-up process.

Please see the attached document for a full scope, mockups and the parent category icons.

Target Market(s)

18-35 Australian event goers

Industry/Entity Type

Events

Number of Pages Required

4 page

```html
<!DOCTYPE html>
<html lang="en">
<head>
<meta charset="utf-8">
<title>Gigora – Email Sign Up</title>
<link rel="stylesheet" href="https://fonts.googleapis.com/css2?family=Oswald:wght@300;400&family=Roboto:ital,wght@0,400;0,500;1,300&family=Questrial&display=swap">
<style>
  :root {
    --brand: #12b3d9;
    --white: #ffffff;
    --field-border: #92e2f4;
    --field-text: #6f6f6f;
    --heading: #5f5f5f;
    --body-text: #4a4a4a;
    --error: #d0021b;
    --button-top: #414141;
    --button-bottom: #1f1f1f;
    --tick: #1aa9d6;
  }
  * { box-sizing: border-box; margin: 0; padding: 0; }
  html, body { width: 1200px; height: 635px; overflow: hidden; background: var(--white); }
  body { position: relative; font-family: "Roboto", sans-serif; }

  .site-header { position: absolute; left: 0; top: 0; width: 1200px; height: 71px; background: var(--brand); }
  .brand-name { position: absolute; left: 75px; top: 4px; font-family: "Oswald", sans-serif; font-weight: 400; font-size: 44px; line-height: 60px; color: var(--white); }
  .main-nav, .account-nav { position: absolute; top: 27px; display: flex; gap: 10px; font-size: 12.5px; font-weight: 400; color: var(--white); letter-spacing: 0.4px; }
  .main-nav { left: 258px; }
  .account-nav { left: 1016px; }
  .divider { opacity: 0.9; }
  .search-box { position: absolute; left: 800px; top: 20px; width: 197px; height: 32px; border-radius: 16px; background: var(--white); border: 2px solid #d8f4fb; }
  .search-box span { position: absolute; left: 19px; top: 6px; font-style: italic; font-weight: 300; font-size: 13.5px; color: #777; }
  .search-box svg { position: absolute; right: 10px; top: 6px; }

  .section-title { position: absolute; top: 130px; font-family: "Oswald", sans-serif; font-weight: 400; font-size: 36px; line-height: 46px; color: var(--heading); letter-spacing: 0; }
  .signup-title { left: 74px; }
  .advantage-title { left: 524px; }

  .signup-form { position: absolute; left: 74px; top: 190px; }
  .field { position: absolute; left: 0; width: 323px; height: 32px; border: 2px solid var(--field-border); border-radius: 16px; padding-left: 17px; font-style: italic; font-weight: 300; font-size: 14px; line-height: 28px; color: var(--field-text); }
  .field-error { position: absolute; left: 330px; font-style: italic; font-weight: 300; font-size: 13px; line-height: 32px; color: var(--error); white-space: nowrap; }
  .submit-button { position: absolute; left: 1px; top: 320px; width: 193px; height: 48px; border-radius: 16px; background: linear-gradient(var(--button-top), var(--button-bottom)); color: var(--white); font-size: 16px; font-weight: 400; letter-spacing: 0.6px; line-height: 48px; text-align: center; }

  .advantage-list { position: absolute; left: 524px; top: 176px; list-style: none; font-family: "Questrial", sans-serif; font-size: 16.5px; color: var(--body-text); }
  .advantage-list li { position: relative; height: 30.5px; line-height: 30.5px; padding-left: 26px; white-space: nowrap; }
  .advantage-list svg { position: absolute; left: 0; top: 10px; }
</style>
</head>
<body>
  <header class="site-header">
    <div class="brand-name">Gigora</div>
    <nav class="main-nav"><span>FIND</span><span class="divider">|</span><span>&nbsp;EVENTS</span></nav>
    <div class="search-box">
      <span>Search..</span>
      <svg width="18" height="16" viewBox="0 0 18 16" aria-hidden="true"><circle cx="6.5" cy="6.5" r="4.8" fill="none" stroke="#555" stroke-width="2"/><line x1="10" y1="10" x2="16" y2="14.5" stroke="#555" stroke-width="3" stroke-linecap="round"/></svg>
    </div>
    <nav class="account-nav"><span>SIGN UP</span><span class="divider">|</span><span>&nbsp;LOG IN</span></nav>
  </header>

  <h1 class="section-title signup-title">EMAIL SIGN UP</h1>
  <form class="signup-form">
    <div class="field" style="top:0">Username</div><div class="field-error" style="top:0">error message</div>
    <div class="field" style="top:42px">Email Address</div><div class="field-error" style="top:42px">error message</div>
    <div class="field" style="top:82px">Password</div>
    <div class="field" style="top:124px">Confirm Password</div>
    <div class="field" style="top:164px">First Name</div>
    <div class="field" style="top:205px">Last Name</div>
    <div class="field" style="top:246px">Date of Brith</div>
    <div class="submit-button">SIGN UP NOW</div>
  </form>

  <h2 class="section-title advantage-title">ADVANTAGE</h2>
  <ul class="advantage-list">
    <li><svg width="14" height="12" viewBox="0 0 14 12" aria-hidden="true"><path d="M1 6.5 L5 10.5 L13 1.5" fill="none" stroke="var(--tick)" stroke-width="2.6" stroke-linejoin="round"/></svg>Get personalised event recommendations</li>
    <li><svg width="14" height="12" viewBox="0 0 14 12" aria-hidden="true"><path d="M1 6.5 L5 10.5 L13 1.5" fill="none" stroke="var(--tick)" stroke-width="2.6" stroke-linejoin="round"/></svg>Get notified about your favourite events – never miss out again</li>
    <li><svg width="14" height="12" viewBox="0 0 14 12" aria-hidden="true"><path d="M1 6.5 L5 10.5 L13 1.5" fill="none" stroke="var(--tick)" stroke-width="2.6" stroke-linejoin="round"/></svg>Follow all your favourite artists, musicians, teams and players in one place</li>
    <li><svg width="14" height="12" viewBox="0 0 14 12" aria-hidden="true"><path d="M1 6.5 L5 10.5 L13 1.5" fill="none" stroke="var(--tick)" stroke-width="2.6" stroke-linejoin="round"/></svg>Follow your favourite local venues to know everything happening there</li>
    <li><svg width="14" height="12" viewBox="0 0 14 12" aria-hidden="true"><path d="M1 6.5 L5 10.5 L13 1.5" fill="none" stroke="var(--tick)" stroke-width="2.6" stroke-linejoin="round"/></svg>Get curated news and feature content on your favourite artists (coming soon)</li>
    <li><svg width="14" height="12" viewBox="0 0 14 12" aria-hidden="true"><path d="M1 6.5 L5 10.5 L13 1.5" fill="none" stroke="var(--tick)" stroke-width="2.6" stroke-linejoin="round"/></svg>Invite your mates to events via Chatterly (CH sign-up only)</li>
  </ul>
</body>
</html>
```